i need a business card for a plumbing company in california

we are a drain cleaning , maintenance plumbing company who is starting new marketing campaign for a tatrench-less pipe installation department .

Target Market(s)

the professional who appreciates time and quality workmanship.

Industry/Entity Type

Plumbing

Colors
0655a3
ec1f27

Requirements
Must have
• the second logo needs to be included
Nice to have
• a focus on the services offered
Should not have
• any underlined words on the brief

```html
<!DOCTYPE html>
<html lang="en">
<head>
<meta charset="utf-8">
<title>Clearline Plumbing – Business Card</title>
<link rel="stylesheet" href="https://fonts.googleapis.com/css2?family=Arimo:wght@400;700&family=Saira:wght@600&display=swap">
<style>
  :root {
    --bg: #e9e8e6;
    --card: #1e1e20;
    --card-back: #1b1b1d;
    --brand-grey: #97948c;
    --text-grey: #b9b7b2;
    --rule: #4a4a4c;
    --red: #e3222a;
    --pattern-a: #2a2a2c;
    --pattern-b: #222224;
  }
  * { box-sizing: border-box; margin: 0; padding: 0; }
  html, body { width: 1200px; height: 1108px; overflow: hidden; }
  body {
    background: var(--bg);
    font-family: "Arimo", Arial, sans-serif;
    position: relative;
  }
  .card {
    position: absolute;
    top: 214px;
    width: 420px;
    height: 680px;
    border-radius: 26px;
    overflow: hidden;
  }
  .card--front { left: 150px; background: var(--card); }
  .card--back { left: 630px; background: var(--card-back); }

  .brand {
    position: absolute;
    left: 0; right: 0;
    top: 170px;
    display: flex;
    align-items: center;
    justify-content: center;
    gap: 14px;
  }
  .brand__dot {
    width: 16px; height: 16px;
    background: var(--red);
    border-radius: 50%;
  }
  .brand__name {
    font-family: "Arimo", Arial, sans-serif;
    font-weight: 700;
    font-size: 40px;
    line-height: 1;
    color: var(--brand-grey);
  }

  .contact {
    position: absolute;
    left: 0; right: 0;
    top: 318px;
    text-align: center;
  }
  .contact__name {
    font-family: "Saira", Arial, sans-serif;
    font-weight: 600;
    font-size: 30px;
    letter-spacing: 0.5px;
    color: var(--red);
    line-height: 1;
  }
  .contact__role {
    margin-top: 6px;
    font-size: 19px;
    color: var(--text-grey);
  }
  .rule {
    width: 220px;
    height: 1px;
    background: var(--rule);
    margin: 14px auto;
  }
  .contact__list { list-style: none; font-size: 19px; color: var(--text-grey); line-height: 26px; }
  .contact__label { color: var(--red); font-weight: 700; }
  .contact__web { color: var(--red); font-weight: 700; font-size: 20px; }
  .address { font-size: 19px; color: var(--text-grey); line-height: 26px; }

  .back-pattern {
    position: absolute;
    inset: 0;
    background: linear-gradient(180deg, var(--pattern-a) 0%, var(--pattern-b) 75%, var(--card-back) 100%);
  }
  .back-brand {
    position: absolute;
    left: 0; right: 0;
    bottom: 110px;
    text-align: center;
    font-family: "Arimo", Arial, sans-serif;
    font-weight: 700;
    font-size: 46px;
    line-height: 1.05;
    color: var(--brand-grey);
  }
</style>
</head>
<body>
  <section class="card card--front" aria-label="Business card front">
    <div class="brand">
      <span class="brand__dot"></span>
      <span class="brand__name">Clearline Plumbing</span>
    </div>
    <div class="contact">
      <h1 class="contact__name">DANIEL REYES</h1>
      <p class="contact__role">Managing Director</p>
      <div class="rule"></div>
      <ul class="contact__list">
        <li><span class="contact__label">P:</span> 044-123 456 789</li>
        <li><span class="contact__label">M:</span> 044-123 456 789</li>
        <li><span class="contact__label">E:</span> info@webname.com</li>
        <li class="contact__web">www.websitename.com</li>
      </ul>
      <div class="rule"></div>
      <p class="address">12345, Address Goes Here<br>Country Name, 123456.</p>
    </div>
  </section>

  <section class="card card--back" aria-label="Business card back">
    <div class="back-pattern" role="img" aria-label="Faint repeating brand-mark pattern in dark grey"></div>
    <p class="back-brand">Clearline<br>Plumbing</p>
  </section>
</body>
</html>
```